Copperleaf Roofing Business Card

This is my current business card. But I’d like to make some changes. Somewhere on the card I’d like to list some of the services we offer. Maybe on the back? But I’d still like to keep the red. White and black modern look.

-residential & commercial roofing
-Roof Repairs & Maintenance
-Storm Damage & Insurance Claims specialist
-Christmas Lights and permanent Christmas lights
Fencing. Windows. Gutters. Siding. Sheetrock, painting.

```html
<!DOCTYPE html>
<html lang="en">
<head>
<meta charset="UTF-8">
<title>Copperleaf Roofing Co. – Business Card</title>
<link href="https://fonts.googleapis.com/css2?family=Poppins:wght@300;400;500;600;700&display=swap" rel="stylesheet">
<style>
  :root {
    --page-bg: #e3e7e8;
    --card-bg: #161616;
    --brand-red: #e31e26;
    --text-white: #ffffff;
    --text-soft: #f1f1f1;
    --emboss: #1d1d1d;
  }
  * { margin: 0; padding: 0; box-sizing: border-box; }
  html, body {
    width: 1200px; height: 960px; overflow: hidden;
    background: var(--page-bg);
    font-family: 'Poppins', sans-serif;
  }
  .canvas { position: relative; width: 1200px; height: 960px; }

  .card {
    position: absolute; left: 250px; width: 702px; height: 400px;
    background: var(--card-bg);
    border-left: 4px solid var(--brand-red);
    border-bottom: 4px solid var(--brand-red);
    border-radius: 30px;
    overflow: hidden;
  }
  .card--front { top: 60px; }
  .card--back { top: 500px; }

  .brand-mark {
    position: absolute; width: 112px; height: 112px;
    border-radius: 50%; background: var(--brand-red);
  }
  .brand-name {
    position: absolute; width: 280px; text-align: center;
    color: var(--text-white); font-weight: 700; font-size: 22px;
    line-height: 1.25; letter-spacing: 1px; text-transform: uppercase;
  }
  .card--front .brand-mark { left: 291px; top: 26px; }
  .card--front .brand-name { left: 207px; top: 150px; }

  .services {
    position: absolute; left: 0; right: 0; top: 238px;
    text-align: center; color: var(--text-soft);
  }
  .services__title {
    color: var(--brand-red); font-weight: 600; font-size: 19px;
    letter-spacing: 0.5px; line-height: 24px;
  }
  .services__list { list-style: none; font-weight: 300; font-size: 16.5px; line-height: 23px; letter-spacing: 0.4px; }

  .card--back .brand-mark { left: 74px; top: 26px; }
  .card--back .brand-name { left: -10px; top: 150px; }

  .person {
    position: absolute; right: 30px; top: 30px; text-align: right;
  }
  .person__name { font-size: 29px; font-weight: 700; letter-spacing: 2px; line-height: 36px; text-transform: uppercase; }
  .person__first { color: var(--brand-red); }
  .person__last { color: var(--text-white); }
  .person__role { color: var(--text-white); font-size: 16px; font-weight: 600; letter-spacing: 1px; }
  .accent-bar {
    position: absolute; right: 0; top: 30px; width: 20px; height: 62px;
    background: var(--brand-red);
  }

  .contact-list {
    position: absolute; left: 26px; top: 304px; list-style: none;
    color: var(--text-white); font-size: 18px; letter-spacing: 0.6px;
  }
  .contact-list li { display: flex; align-items: center; height: 22.5px; }
  .contact-list svg { width: 16px; height: 16px; margin-right: 12px; fill: var(--brand-red); }

  .emboss-circle {
    position: absolute; left: 506px; top: 202px; width: 188px; height: 188px;
    border-radius: 50%; background: var(--emboss);
    box-shadow: inset 1px 1px 2px rgba(255,255,255,0.04), inset -2px -2px 4px rgba(0,0,0,0.4);
  }
</style>
</head>
<body>
<div class="canvas">

  <section class="card card--front">
    <div class="brand-mark"></div>
    <div class="brand-name">Copperleaf<br>Roofing Co.</div>
    <div class="services">
      <h2 class="services__title">SERVICES WE OFFER</h2>
      <ul class="services__list">
        <li>Roof Repairs &amp; Maintenance</li>
        <li>Residential &amp; Commercial Roofing</li>
        <li>Storm Damage &amp; Insurance Claims Specialist</li>
        <li>Christmas Lights and Permanent Christmas lights</li>
        <li>Fencing. Windows. Gutters. Siding. Sheetrock, Painting</li>
      </ul>
    </div>
  </section>

  <section class="card card--back">
    <div class="brand-mark"></div>
    <div class="brand-name">Copperleaf<br>Roofing Co.</div>

    <div class="person">
      <div class="person__name"><span class="person__first">Dana</span> <span class="person__last">Whitlock</span></div>
      <div class="person__role">OWNER</div>
    </div>
    <div class="accent-bar"></div>

    <div class="emboss-circle"></div>

    <ul class="contact-list">
      <li>
        <svg viewBox="0 0 24 24"><path d="M6.6 10.8a15.1 15.1 0 0 0 6.6 6.6l2.2-2.2c.3-.3.7-.4 1-.2 1.1.4 2.3.6 3.6.6.6 0 1 .4 1 1V20c0 .6-.4 1-1 1A17 17 0 0 1 3 4c0-.6.4-1 1-1h3.5c.6 0 1 .4 1 1 0 1.3.2 2.5.6 3.6.1.3 0 .7-.2 1z"/></svg>
        555-014-2278
      </li>
      <li>
        <svg viewBox="0 0 24 24"><path d="M12 2a10 10 0 1 0 0 20 10 10 0 0 0 0-20zm6.9 6h-2.9a15.6 15.6 0 0 0-1.4-3.6A8 8 0 0 1 18.9 8zM12 4c.8 1.2 1.5 2.5 1.9 4h-3.8c.4-1.4 1.1-2.8 1.9-4zM4.3 14a8 8 0 0 1 0-4h3.4a16.5 16.5 0 0 0 0 4zm.8 2h2.9c.3 1.3.8 2.5 1.4 3.6A8 8 0 0 1 5.1 16zM8 8H5.1a8 8 0 0 1 4.3-3.6C8.8 5.5 8.4 6.7 8 8zm4 12c-.8-1.2-1.5-2.5-1.9-4h3.8c-.4 1.4-1.1 2.8-1.9 4zm2.3-6H9.7a14.7 14.7 0 0 1 0-4h4.6a14.7 14.7 0 0 1 0 4zm.3 5.6c.6-1.1 1.1-2.3 1.4-3.6h2.9a8 8 0 0 1-4.3 3.6zm1.7-5.6a16.5 16.5 0 0 0 0-4h3.4a8 8 0 0 1 0 4z"/></svg>
        www.copperleafroofing.co
      </li>
      <li>
        <svg viewBox="0 0 24 24"><path d="M3 6h18c.6 0 1 .4 1 1v11c0 .6-.4 1-1 1H3c-.6 0-1-.4-1-1V7c0-.6.4-1 1-1zm1 2.2V17h16V8.2l-8 5.3z"/></svg>
        dana@copperleafroofing.co
      </li>
    </ul>
  </section>

</div>
</body>
</html>
```